Letterhead Design for Law Firm

**Edit: I have added the photo of a bottom that I like.

------
We are looking for a re-design of our new letterhead. The letterhead is for a law firm and will be used for digital and traditionally printed correspondence.

Here are some suggestions:

- Please use colours are #8ec900 and simple black.
- Please do not use any type of "waves" at the bottom of the page. This is not in style at all.
- Please stay modern yet conservative.
- Please use font Segoe UI Light or similar if you can
- Avoid clipart or illustrations.
- Utilize ample white space in the layout so the design looks clean and information is easy to read at a glance. Don't overcrowd the letterhead.
- Make sure the letterhead design is consistent with our brand identity (see corvelith.ca)
-Please, no black headers or footers.

I am attaching my current letterhead and signature for your convenience.

Remember, the letterhead is an extension of our professional identity. We are a successful firm and trial lawyers who correspond with insurers, judges, lawyers, courts, clients, etc. Make it new, modern, attractive, yet powerful and conservative.

It needs to be easily printable. I would like the bleed removed in print so the black bar the bottom crosses the page (but the text is not near the edges)
Updates

Low design quality

Target Market(s)

Clients, Government Offices, Judiciary, Lawyers, Insurance Companies, Colleagues.

Industry/Entity Type

Law

Other font styles liked:
• Segoe UI LIght, Calibri Light,

Colors
00AB8E
00BBA5
67D7C9
C6EFE9
E9F9F6

Requirements
Must have
• Everything that is on the letterhead now.
Nice to have
• Cutting Edge design, yet conservative.
Should not have
• law firm cliche design, images,

```html
<!DOCTYPE html>
<html lang="en">
<head>
<meta charset="utf-8">
<title>Corvelith Personal Injury Lawyers – Letterhead</title>
<link rel="stylesheet" href="https://fonts.googleapis.com/css2?family=Carlito:wght@400;700&family=Open+Sans:wght@400;600;700&display=swap">
<style>
  :root {
    --green: #8ec900;
    --ink: #111111;
    --text: #333333;
    --paper: #ffffff;
    --band: #000000;
  }
  * { margin: 0; padding: 0; box-sizing: border-box; }
  html, body { width: 925px; height: 1200px; overflow: hidden; background: var(--paper); }
  .letterhead {
    position: relative; width: 925px; height: 1200px; overflow: hidden;
    background: var(--paper); color: var(--text);
    font-family: "Carlito", "Calibri", sans-serif; font-size: 17.5px;
  }
  .brand {
    position: absolute; left: 0; top: 62px; width: 925px;
    display: flex; justify-content: center; align-items: center; gap: 12px;
  }
  .brand-mark { width: 14px; height: 14px; background: var(--green); }
  .brand-name {
    font-family: "Carlito", sans-serif; font-weight: 700; color: var(--ink);
    font-size: 32px; line-height: 40px; letter-spacing: 1px; white-space: nowrap;
  }
  .practice-areas {
    position: absolute; left: 32px; top: 136px; width: 858px;
    display: flex; justify-content: space-between;
    font-family: "Open Sans", sans-serif; font-size: 13px; color: #222; white-space: nowrap;
  }
  .practice-areas .sep { color: var(--green); }
  .header-rule { position: absolute; left: 31px; top: 163px; width: 859px; height: 1.5px; background: var(--ink); }

  .line { position: absolute; left: 32px; white-space: nowrap; line-height: 22px; }
  .strong { font-weight: 700; }
  .re-detail { left: 303px; font-weight: 700; }
  .re-detail sup { font-size: 10px; line-height: 0; vertical-align: 7px; }

  .closing { position: absolute; left: 35px; font-family: "Open Sans", sans-serif; white-space: nowrap; }
  .closing.greet { top: 862px; font-size: 15px; color: #333; }
  .closing.firm { top: 885px; font-family: "Carlito", sans-serif; font-size: 16.5px; color: #111; }
  .signature { position: absolute; left: 35px; top: 910px; width: 200px; height: 50px; background: linear-gradient(90deg, #e9e9e9, #f6f6f6); }
  .closing.signer { top: 960px; font-size: 15px; color: #333; }
  .closing.corp { top: 982px; font-family: "Carlito", sans-serif; font-size: 14px; color: #111; }
  .closing.small { font-size: 12px; color: #333; }

  .footer { position: absolute; left: 0; top: 1060px; width: 925px; height: 140px; background: var(--band); border-top: 3px solid var(--green); }
  .contact { position: absolute; top: 24px; transform: translateX(-50%); text-align: center; color: #fff; font-family: "Open Sans", sans-serif; font-size: 13px; font-weight: 700; line-height: 18px; white-space: nowrap; }
  .contact svg { display: block; margin: 0 auto 14px; width: 28px; height: 26px; fill: var(--green); }
  .contact .light { font-weight: 400; }
</style>
</head>
<body>
<main class="letterhead">
  <header>
    <div class="brand">
      <span class="brand-mark"></span>
      <span class="brand-name">CORVELITH PERSONAL INJURY LAWYERS</span>
    </div>
    <nav class="practice-areas">
      <span>Serious Personal Injury</span><span class="sep">|</span>
      <span>Wrongful Death Litigation</span><span class="sep">|</span>
      <span>Long-Term Disability Litigation</span><span class="sep">|</span>
      <span>Wrongful Dismissal Litigation</span><span class="sep">|</span>
      <span>Employee Terminations</span>
    </nav>
    <div class="header-rule"></div>
  </header>

  <section class="letter">
    <div class="line strong" style="top:185px">Without Prejudice</div>
    <div class="line" style="top:228px">March 13, 2024</div>
    <div class="line strong" style="top:272px">By Email</div>
    <div class="line" style="top:315px">Northvale Insurance Company,</div>
    <div class="line" style="top:337px">Claims Litigation Department,</div>
    <div class="line" style="top:359px">48 Alder Crescent North,</div>
    <div class="line" style="top:381px">P.O. Box 3100,</div>
    <div class="line" style="top:403px">Waterloo, ON&nbsp; N2K 7T2.</div>
    <div class="line" style="top:447px"><span class="strong">Attention:</span>&nbsp; Mr. Elias Fenwick</div>
    <div class="line" style="top:490px">Mr. Fenwick:</div>
    <div class="line strong" style="top:534px">Re:</div>
    <div class="line re-detail" style="top:534px">Harlow v. Mercer et al.</div>
    <div class="line re-detail" style="top:556px">DOL:&nbsp; September 12, 2019</div>
    <div class="line re-detail" style="top:578px">Pre-Mediation Settlement Proposal – March 13<sup>th</sup>, 2024</div>
  </section>

  <section class="sign-off">
    <div class="closing greet">Yours very truly,</div>
    <div class="closing firm">CORVELITH PERSONAL INJURY LAWYERS</div>
    <div class="signature" role="img" aria-label="Handwritten signature of Dorian K. Corvelith"></div>
    <div class="closing signer">Dorian K. Corvelith</div>
    <div class="closing corp">Corvelith Law Professional Corporation</div>
    <div class="closing small" style="top:999px">/md</div>
    <div class="closing small" style="top:1017px">Encl.</div>
  </section>

  <footer class="footer">
    <div class="contact" style="left:90px">
      <svg viewBox="0 0 28 28"><circle cx="14" cy="14" r="12" fill="none" stroke="#8ec900" stroke-width="2.5"/><path d="M2 14h24M14 2v24M5 8h18M5 20h18" stroke="#8ec900" stroke-width="2" fill="none"/><ellipse cx="14" cy="14" rx="6" ry="12" fill="none" stroke="#8ec900" stroke-width="2"/></svg>
      www.corvelith.ca
    </div>
    <div class="contact" style="left:267px">
      <svg viewBox="0 0 28 28"><path d="M14 1C8.5 1 5 5 5 10c0 7 9 17 9 17s9-10 9-17c0-5-3.5-9-9-9zm0 13a4 4 0 1 1 0-8 4 4 0 0 1 0 8z"/></svg>
      27 Harbour Street E., Suite 902<br>Hamilton, ON&nbsp; L8N 3C5
    </div>
    <div class="contact" style="left:428px">
      <svg viewBox="0 0 28 28"><path d="M7 2l4 0 2 7-3 2c1.5 3.5 4 6 7 7l2-3 7 2v4c0 2-2 4-4 3C12 23 5 16 4 6c-1-2 1-4 3-4z"/></svg>
      905-555-0142
    </div>
    <div class="contact" style="left:545px">
      <svg viewBox="0 0 28 28"><path d="M8 2h12v9H8zM2 13h24v11H2z"/><path d="M10 5h8M10 8h8" stroke="#000" stroke-width="1.5"/><rect x="6" y="18" width="16" height="2" fill="#000"/></svg>
      905-555-0178
    </div>
    <div class="contact" style="left:670px">
      <svg viewBox="0 0 28 28"><circle cx="14" cy="8" r="6"/><path d="M3 27c0-7 5-12 11-12s11 5 11 12z"/></svg>
      File Clerk:<br><span class="light">Marla Dunstan</span>
    </div>
    <div class="contact" style="left:816px">
      <svg viewBox="0 0 36 26" style="width:36px"><path d="M0 0h36v26H0z"/><path d="M1 1l17 13L35 1M1 25l12-12M35 25L23 13" stroke="#000" stroke-width="2.5" fill="none"/></svg>
      marla@corvelith.ca
    </div>
  </footer>
</main>
</body>
</html>
```